Product Designer Business Card

Small product design, engineering and prototyping firm in need of a clean, professional business card design. To support our 3D design and drawing services, we offer 3D printing, molding, and casting of plastics, silicones, resins, etc. Our logo can still be modified/changed if necessary. The red/orange color is preferred, but may be substituted with blue or green, potentially. Either way, the colour of the logo should be match/compliment colors used throughout the design. One thought is to have the logo/contact info on one side, with the other side describing services offered, like with a small icon of 3D printer, molding, casting, and computer with a 3D model on-screen.
Industry/Entity Type
Mechanical Engineering
Contact Information for Business Card
Company: Kelvar Design
Phone: 613-582-9047
Email: mark@kelvardesign.ca

```html
<!DOCTYPE html>
<html lang="en">
<head>
<meta charset="utf-8">
<title>Kelvar Design – Business Card</title>
<link href="https://fonts.googleapis.com/css2?family=Work+Sans:wght@400;500;600&display=swap" rel="stylesheet">
<style>
  :root {
    --brand-red: #e0260f;
    --brand-red-light: #e8432b;
    --brand-tint: #fbe3df;
    --brand-tint-deep: #f6cdc6;
    --ink: #3a2a26;
    --ink-soft: #6b605c;
    --paper: #ffffff;
    --backdrop: #e6e4e2;
  }
  * { margin: 0; padding: 0; box-sizing: border-box; }
  html, body {
    width: 1200px; height: 716px; overflow: hidden;
    background: var(--backdrop);
    font-family: "Work Sans", sans-serif;
  }
  .canvas {
    position: relative; width: 1200px; height: 716px;
    display: flex; align-items: center; justify-content: center; gap: 40px;
  }
  .card {
    position: relative; width: 520px; height: 297px;
    box-shadow: 0 6px 18px rgba(0,0,0,0.15);
  }
  .card--front {
    background: linear-gradient(135deg, var(--brand-red), var(--brand-red-light));
    display: flex; align-items: center; justify-content: center;
  }
  .wordmark {
    display: flex; align-items: center; gap: 14px;
    color: var(--paper); font-weight: 500; font-size: 40px; letter-spacing: 2px;
  }
  .wordmark__dot {
    width: 30px; height: 30px; border-radius: 50%; background: var(--paper);
  }
  .card--back { background: var(--paper); }
  .services {
    position: absolute; top: 44px; left: 150px;
    display: flex; gap: 38px;
  }
  .service { display: flex; flex-direction: column; align-items: center; gap: 10px; }
  .service__art {
    width: 82px; height: 78px; border-radius: 6px;
    background: linear-gradient(160deg, var(--brand-tint), var(--brand-tint-deep));
  }
  .service__label { font-size: 15px; font-weight: 500; color: var(--ink); }
  .identity {
    position: absolute; left: 40px; bottom: 52px; text-align: right;
  }
  .identity__name {
    font-size: 15px; font-weight: 500; color: var(--brand-red); letter-spacing: 0.5px;
  }
  .identity__role { font-size: 13px; color: var(--ink-soft); letter-spacing: 1px; }
  .divider {
    position: absolute; left: 200px; bottom: 40px;
    width: 1.5px; height: 46px; background: var(--brand-red);
  }
  .contact {
    position: absolute; left: 218px; bottom: 40px;
    font-size: 14px; color: var(--ink-soft); letter-spacing: 0.5px; line-height: 1.55;
  }
  .contact__row { display: flex; align-items: center; gap: 7px; }
  .contact__icon { width: 11px; height: 11px; }
</style>
</head>
<body>
<main class="canvas">
  <section class="card card--front">
    <div class="wordmark"><span class="wordmark__dot"></span><span>Kelvar Design</span></div>
  </section>

  <section class="card card--back">
    <div class="services">
      <div class="service">
        <div class="service__art" role="img" aria-label="Red line icon of a molding press"></div>
        <span class="service__label">Molding</span>
      </div>
      <div class="service">
        <div class="service__art" role="img" aria-label="Red line icon of a 3D printer"></div>
        <span class="service__label">3D printer</span>
      </div>
      <div class="service">
        <div class="service__art" role="img" aria-label="Red line icon representing casting"></div>
        <span class="service__label">Casting</span>
      </div>
    </div>

    <div class="identity">
      <div class="identity__name">DANIEL BROOKS</div>
      <div class="identity__role">President</div>
    </div>
    <div class="divider"></div>
    <div class="contact">
      <div class="contact__row">
        <svg class="contact__icon" viewBox="0 0 12 12"><path d="M3 1 L5 3.5 L4 5 Q5 7 7 8 L8.5 7 L11 9 L9.5 11 Q4 10.5 1 3 Z" fill="#e0260f"/></svg>
        <span>613-582-9047</span>
      </div>
      <div class="contact__row">
        <svg class="contact__icon" viewBox="0 0 12 12" fill="none" stroke="#e0260f" stroke-width="1.4"><rect x="1" y="2.5" width="10" height="7"/><path d="M1 2.5 L6 6.5 L11 2.5"/></svg>
        <span>mark@kelvardesign.ca</span>
      </div>
    </div>
  </section>
</main>
</body>
</html>
```